UI/ UX Design for ERP Software

We need a new UX/UI interface for a ERP software for property managers. Our CMMS / ERP solution is made based on responsive design technologies and is coded in PHP.
The overall UX to be similar to Tev Ulna - easy navigation, intuitive menus.

Industry/Entity Type

Property Management

Number of Pages Required

5+ page

Requirements
Must have
• Round dock buttons
Consistent icons across the application
Enough Spacing between buttons/icons/ menu
Consistent Font
Nice to have
• We would like the UX to allow the users to use the application without /minimum training.
Should not have
• we don't want anything that is classic with respect to UX

```html
<!DOCTYPE html>
<html lang="en">
<head>
<meta charset="utf-8">
<title>Active Dashboard</title>
<link href="https://fonts.googleapis.com/css2?family=Mulish:wght@300;400;500;600;700&family=Varela+Round&display=swap" rel="stylesheet">
<style>
:root{
  --blue:#0a7cf6;
  --ink:#1f2d3a;
  --text:#4a5563;
  --muted:#6b7480;
  --line:#e3e6ea;
  --grid:#9aa7b6;
  --footer:#f2f3f5;
  --c-green:#8ee07f;
  --c-orange:#f0a463;
  --c-dark:#3b3d45;
  --c-violet:#8684f0;
  --c-pink:#f05a7e;
  --c-yellow:#e6d452;
}
*{box-sizing:border-box;margin:0;padding:0}
html,body{width:1200px;height:888px;overflow:hidden;background:#fff}
body{position:relative;font-family:"Mulish",sans-serif;color:var(--ink)}
.abs{position:absolute}
.header{left:0;top:0;width:1200px;height:79px;border-bottom:1px solid var(--line)}
.brand{left:20px;top:20px;display:flex;align-items:center;gap:10px;font-size:30px;font-weight:700;color:var(--blue);letter-spacing:-.5px}
.brand-mark{width:22px;height:22px;background:var(--blue);border-radius:3px}
.header-divider{left:225px;top:0;width:1px;height:79px;background:var(--line)}
.page-title{left:257px;top:17px;display:flex;align-items:center;gap:18px;font-size:27px;font-weight:500;color:#112a3c}
.search{left:627px;top:19px;width:532px;height:40px;border:1px solid #7ab2ef;border-radius:20px;display:flex;align-items:center;padding-left:22px;gap:12px;color:#98a1ab;font-size:13.5px}
.nav{left:0;top:79px;width:1200px;height:70px;border-bottom:1px solid var(--line)}
.nav a{position:absolute;top:26px;font-size:13.5px;color:var(--text);text-decoration:none;letter-spacing:.3px}
.nav a.active{color:var(--blue)}
.nav a.more{color:var(--blue);text-decoration:underline;font-weight:600}
.sidebar{left:0;top:149px;width:226px;height:739px;border-right:1px solid var(--line)}
.range{position:absolute;left:29px;width:150px;height:54px;border-radius:6px;background:#fff;box-shadow:0 2px 8px rgba(20,40,70,.12);display:flex;align-items:center;gap:10px;padding-left:18px;font-size:13px;color:#3a4654;letter-spacing:-.2px}
.range.active{background:var(--blue);color:#fff;padding-left:13px;box-shadow:0 3px 10px rgba(10,124,246,.3)}
.side-rule{position:absolute;left:0;width:225px;height:1px;background:var(--line)}
.stat-label{position:absolute;font-size:10px;font-weight:500;color:#1b2430}
.stat-value{position:absolute;display:flex;align-items:center;gap:8px;font-size:14.5px;font-weight:500;color:#2f3e52}
.range-title{left:257px;top:182px;display:flex;align-items:center;gap:32px;font-size:29px;font-weight:300;color:#0f1e2c;letter-spacing:-.5px}
.chart{left:270px;top:265px}
.legend{left:267px;top:724px;width:930px;height:34px}
.legend-item{position:absolute;top:0;display:flex;gap:4px;font-family:"Varela Round",sans-serif;font-size:10px;line-height:15px;color:#4a5260}
.legend-item i{display:block;width:18px;height:16px;flex:none}
.footer{left:226px;top:843px;width:974px;height:45px;background:var(--footer);font-size:11px;color:#4a5563}
.footer .copy{position:absolute;left:409px;top:15px}
.footer .code{position:absolute;left:917px;top:15px}
</style>
</head>
<body>

<header class="abs header"></header>
<div class="abs brand"><span class="brand-mark"></span>Keyholm</div>
<div class="abs header-divider"></div>
<div class="abs page-title">
  <svg width="36" height="40" viewBox="0 0 36 40" fill="none" stroke="#1a8cf7" stroke-width="2.4" stroke-linejoin="round"><path d="M3 18 L18 4 L33 18"/><path d="M8 14 V37 H15 V26 H21 V37 H28 V14"/><path d="M26 6 V12"/></svg>
  <span>Active Dashboard</span>
</div>
<div class="abs search">
  <svg width="15" height="15" viewBox="0 0 15 15" fill="none" stroke="#7f8893" stroke-width="1.6"><circle cx="6" cy="6" r="4.8"/><path d="M9.6 9.6 L14 14"/></svg>
  <span>Search</span>
</div>

<nav class="abs nav">
  <a class="active" style="left:34px">Dashboard</a>
  <a style="left:138px">Customers</a>
  <a style="left:238px;top:24px">Properties</a>
  <a style="left:336px">Tenants</a>
  <a style="left:418px">Contacts</a>
  <a style="left:507px">Contractors</a>
  <a style="left:614px;top:24px">Employees</a>
  <a style="left:715px;top:24px">Compliance Management</a>
  <a style="left:909px">Prevent. Maintenance</a>
  <a class="more" style="left:1082px;top:24px">VIEW MORE</a>
</nav>

<aside class="abs sidebar">
  <div class="range active" style="top:15px">
    <svg width="20" height="20" viewBox="0 0 20 20" fill="none" stroke="#fff" stroke-width="1.5"><circle cx="10" cy="10" r="8.5"/><path d="M10 4 V10 L7 13"/></svg>LAST 7 DAYS
  </div>
  <div class="range" style="top:84px">
    <svg width="20" height="20" viewBox="0 0 20 20" fill="none" stroke="var(--blue)" stroke-width="1.5"><circle cx="10" cy="10" r="8.5"/><path d="M10 4 V10 L7 13"/></svg>LAST MONTHS
  </div>
  <div class="range" style="top:155px">
    <svg width="20" height="20" viewBox="0 0 20 20" fill="none" stroke="var(--blue)" stroke-width="1.5"><circle cx="10" cy="10" r="8.5"/><path d="M10 4 V10 L7 13"/></svg>LAST 3 MONTHS
  </div>
  <div class="range" style="top:221px">
    <svg width="20" height="20" viewBox="0 0 20 20" fill="none" stroke="var(--blue)" stroke-width="1.5"><circle cx="10" cy="10" r="8.5"/><path d="M10 4 V10 L7 13"/></svg>NEXT 7 DAYS
  </div>
  <div class="range" style="top:293px">
    <svg width="20" height="20" viewBox="0 0 20 20" fill="none" stroke="var(--blue)" stroke-width="1.5"><circle cx="10" cy="10" r="8.5"/><path d="M10 4 V10 L7 13"/></svg>NEXT MONTHS
  </div>

  <div class="side-rule" style="top:373px"></div>
  <div class="stat-label" style="left:22px;top:394px">PROPERTIES</div>
  <div class="stat-label" style="left:121px;top:394px">TENANTS</div>
  <div class="stat-value" style="left:20px;top:424px">
    <svg width="17" height="17" viewBox="0 0 17 17" fill="none" stroke="var(--blue)" stroke-width="1.3" stroke-linejoin="round"><path d="M1 8 L8.5 1.5 L16 8"/><path d="M3.5 6 V16 H7 V11 H10 V16 H13.5 V6"/></svg>3
  </div>
  <div class="stat-value" style="left:120px;top:424px">
    <svg width="14" height="17" viewBox="0 0 14 17" fill="none" stroke="var(--blue)" stroke-width="1.3"><circle cx="7" cy="5" r="3.6"/><path d="M1 16 V13 Q1 10 4 10 H10 Q13 10 13 13 V16 Z"/></svg>8
  </div>

  <div class="side-rule" style="top:463px"></div>
  <div class="stat-label" style="left:22px;top:488px">TOTAL PROPERTIES AREA</div>
  <div class="stat-value" style="left:22px;top:517px">
    <svg width="16" height="16" viewBox="0 0 16 16" fill="none" stroke="var(--blue)" stroke-width="1.3"><rect x="2.5" y="2.5" width="11" height="11"/><path d="M0.5 2.5 H4.5 M2.5 0.5 V4.5 M11.5 2.5 H15.5 M13.5 0.5 V4.5 M0.5 13.5 H4.5 M2.5 11.5 V15.5 M11.5 13.5 H15.5 M13.5 11.5 V15.5"/></svg>422,000.00 sq.ft
  </div>

  <div class="side-rule" style="top:560px"></div>
  <div class="stat-label" style="left:27px;top:580px">RENTAL AREA</div>
  <div class="stat-value" style="left:28px;top:610px">
    <svg width="16" height="16" viewBox="0 0 16 16" fill="none" stroke="var(--blue)" stroke-width="1.3"><rect x="2.5" y="2.5" width="11" height="11"/><path d="M0.5 2.5 H4.5 M2.5 0.5 V4.5 M11.5 2.5 H15.5 M13.5 0.5 V4.5 M0.5 13.5 H4.5 M2.5 11.5 V15.5 M11.5 13.5 H15.5 M13.5 11.5 V15.5"/></svg>233,500.00 sq.ft.
  </div>

  <div class="side-rule" style="top:650px"></div>
  <div class="stat-label" style="left:30px;top:669px">VACANCIES AREA</div>
  <div class="stat-value" style="left:30px;top:699px">
    <svg width="16" height="16" viewBox="0 0 16 16" fill="none" stroke="var(--blue)" stroke-width="1.3"><rect x="2.5" y="2.5" width="11" height="11"/><path d="M0.5 2.5 H4.5 M2.5 0.5 V4.5 M11.5 2.5 H15.5 M13.5 0.5 V4.5 M0.5 13.5 H4.5 M2.5 11.5 V15.5 M11.5 13.5 H15.5 M13.5 11.5 V15.5"/></svg>188,500.00 sq.ft.
  </div>
</aside>

<div class="abs range-title">
  <svg width="18" height="20" viewBox="0 0 18 20" fill="var(--blue)"><rect x="1" y="9" width="3.4" height="11"/><rect x="7.3" y="1" width="3.4" height="19"/><rect x="13.6" y="6" width="3.4" height="14"/></svg>
  <span>12/27/2020 - 01/03/2021</span>
</div>

<svg class="abs chart" width="930" height="410" viewBox="270 265 930 410" font-family="Mulish, sans-serif" font-size="10.5" fill="#3a4654">
  <g fill="#4a5563">
    <rect x="276" y="273" width="22" height="3.4" rx="1.5"/>
    <rect x="276" y="280" width="22" height="3.4" rx="1.5"/>
    <rect x="276" y="287" width="22" height="3.4" rx="1.5"/>
  </g>
  <g stroke="var(--grid)" stroke-width="0.8">
    <line x1="341" y1="287" x2="1195" y2="287"/>
    <line x1="341" y1="355" x2="1195" y2="355"/>
    <line x1="341" y1="425" x2="1195" y2="425"/>
    <line x1="341" y1="494" x2="1195" y2="494"/>
    <line x1="341" y1="563" x2="1195" y2="563"/>
  </g>
  <g stroke="#7d8894" stroke-width="1">
    <line x1="341" y1="632" x2="1195" y2="632"/>
    <line x1="341" y1="632" x2="341" y2="644"/>
    <line x1="448" y1="632" x2="448" y2="644"/>
    <line x1="555" y1="632" x2="555" y2="644"/>
    <line x1="661" y1="632" x2="661" y2="644"/>
    <line x1="768" y1="632" x2="768" y2="644"/>
    <line x1="875" y1="632" x2="875" y2="644"/>
    <line x1="982" y1="632" x2="982" y2="644"/>
    <line x1="1089" y1="632" x2="1089" y2="644"/>
    <line x1="1195" y1="632" x2="1195" y2="644"/>
  </g>
  <g>
    <text x="306" y="290">1.25</text>
    <text x="306" y="359">1</text>
    <text x="306" y="429">0.75</text>
    <text x="306" y="498">0.5</text>
    <text x="306" y="567">0.25</text>
    <text x="306" y="637">0</text>
  </g>
  <rect x="671" y="345" width="6" height="287" fill="var(--blue)"/>
  <g text-anchor="middle">
    <text x="394" y="670">12/27/2020</text>
    <text x="501" y="670">12/28/2020</text>
    <text x="608" y="670">12/29/2020</text>
    <text x="715" y="670">12/30/2020</text>
    <text x="822" y="670">12/31/2020</text>
    <text x="928" y="670">01/01/2021</text>
    <text x="1035" y="670">02/01/2021</text>
    <text x="1142" y="670">03/01/2021</text>
  </g>
</svg>

<div class="abs legend">
  <div class="legend-item" style="left:0"><i style="background:var(--blue)"></i><span>Scheduled<br>Maintenance</span></div>
  <div class="legend-item" style="left:109px"><i style="background:var(--c-green)"></i><span>Completed Scheduled<br>Maintenance</span></div>
  <div class="legend-item" style="left:262px"><i style="background:var(--c-orange)"></i><span>Future Scheduled<br>Maintenance</span></div>
  <div class="legend-item" style="left:394px"><i style="background:var(--c-dark)"></i><span>Scheduled Work<br>Orders</span></div>
  <div class="legend-item" style="left:518px"><i style="background:var(--c-violet)"></i><span>Completed Work<br>Orders</span></div>
  <div class="legend-item" style="left:643px"><i style="background:var(--c-pink)"></i><span>Property Inspections<br>in Progress</span></div>
  <div class="legend-item" style="left:791px"><i style="background:var(--c-yellow)"></i><span>Completed Property<br>Inspections</span></div>
</div>

<footer class="abs footer">
  <span class="copy">Copyrights © 2020 All Rights Reserved</span>
  <span class="code">C44</span>
</footer>

</body>
</html>
```